Unique Business Card Design

Unique Business Card design for our orthotic and prosthetic company. Our logo is on our website, color is light blue. Unique shape (artificial leg shaped, vertical, etc..) preferred. Logo, business name, individual name and basic demographics needed.

Industry/Entity Type

Business

Contact Information for Business Card

Logo, Industry, Phone # Logo, "Prosthetic & Orthotic Services" Place to add individual name and contact info

Colors
cee9f5

Requirements
Must have
• The icon must be there, placement of "Prosthetic & Orthotic Services" can be moved
Nice to have
• Like the mix of light blue, and a little darker blue. One design included the icons from my website which was a nice touch

```html
<!DOCTYPE html>
<html lang="en">
<head>
<meta charset="utf-8">
<title>LimbWorks Inc. – Business Card</title>
<link href="https://fonts.googleapis.com/css2?family=Arimo:wght@400;700&display=swap" rel="stylesheet">
<style>
  :root {
    --stage: #3b3b3b;
    --card-white: #ffffff;
    --brand-blue: #1f66b3;
    --brand-blue-dark: #17528f;
    --mist: #d6dbe1;
    --circle: rgba(255,255,255,0.86);
    --text-light: #ffffff;
  }
  * { box-sizing: border-box; margin: 0; padding: 0; }
  html, body {
    width: 1200px; height: 950px; overflow: hidden;
    background: var(--stage);
    font-family: "Arimo", Arial, sans-serif;
  }
  .stage {
    position: relative; width: 1200px; height: 950px;
    display: flex; flex-direction: column; align-items: center; justify-content: center; gap: 50px;
  }
  .card {
    position: relative; width: 700px; height: 400px;
    border-radius: 26px; overflow: hidden;
    box-shadow: 0 14px 30px rgba(0,0,0,0.45);
  }

  /* Front */
  .card--front { background: var(--card-white); }
  .front-lockup {
    position: absolute; left: 120px; top: 50%; transform: translateY(-50%);
    display: flex; align-items: center; gap: 26px;
  }
  .brand-dot {
    width: 150px; height: 150px; border-radius: 50%;
    background: var(--brand-blue);
  }
  .brand-name {
    color: var(--brand-blue); font-weight: 700; font-size: 40px; letter-spacing: 0.5px;
    line-height: 1; padding-bottom: 8px; border-bottom: 2px solid var(--brand-blue);
  }
  .brand-tagline {
    color: var(--brand-blue); font-size: 20px; margin-top: 8px; padding-left: 14px;
  }

  /* Back */
  .card--back {
    background: linear-gradient(90deg, var(--brand-blue) 0 62%, var(--mist) 62% 100%);
  }
  .back-circle {
    position: absolute; left: 330px; top: -10px; width: 400px; height: 400px; border-radius: 50%;
    background: var(--circle);
  }
  .back-lockup {
    position: absolute; left: 360px; top: 150px;
    display: flex; align-items: center; gap: 14px;
  }
  .back-lockup .brand-dot { width: 70px; height: 70px; }
  .back-lockup .brand-name { font-size: 26px; padding-bottom: 5px; }
  .back-lockup .brand-tagline { font-size: 14px; margin-top: 5px; padding-left: 8px; }

  .holder {
    position: absolute; left: 48px; top: 70px; color: var(--text-light);
  }
  .holder-name { font-size: 26px; font-weight: 700; letter-spacing: 0.5px; }
  .holder-title { font-size: 18px; font-weight: 700; margin-top: 4px; }
  .holder-address { font-size: 17px; line-height: 1.35; margin-top: 20px; }
  .contact-list { list-style: none; margin-top: 14px; }
  .contact-list li {
    display: flex; align-items: center; gap: 10px; font-size: 17px; line-height: 1.5;
  }
  .contact-list svg { width: 16px; height: 16px; fill: var(--text-light); flex: none; }
</style>
</head>
<body>
<main class="stage">

  <section class="card card--front" aria-label="Card front">
    <div class="front-lockup">
      <div class="brand-dot"></div>
      <div>
        <div class="brand-name">LIMBWORKS INC.</div>
        <div class="brand-tagline">Prosthetic &amp; Orthotic Services</div>
      </div>
    </div>
  </section>

  <section class="card card--back" aria-label="Card back">
    <div class="back-circle"></div>
    <div class="back-lockup">
      <div class="brand-dot"></div>
      <div>
        <div class="brand-name">LIMBWORKS INC.</div>
        <div class="brand-tagline">Prosthetic &amp; Orthotic Services</div>
      </div>
    </div>

    <div class="holder">
      <h1 class="holder-name">MIRA CASTELLAN</h1>
      <p class="holder-title">CO LPO</p>
      <p class="holder-address">2380 Alder Row<br>Fairview, NY 11990</p>
      <ul class="contact-list">
        <li>
          <svg viewBox="0 0 16 16" aria-hidden="true"><path d="M1 5c0-2 3-3 7-3s7 1 7 3v1h-4V5H5v1H1z"/><rect x="3" y="7" width="10" height="7" rx="1"/></svg>
          555.014.2200
        </li>
        <li>
          <svg viewBox="0 0 16 16" aria-hidden="true"><path d="M4 0h8a1 1 0 0 1 1 1v14a1 1 0 0 1-1 1H4a1 1 0 0 1-1-1V1a1 1 0 0 1 1-1zm1 2v10h6V2z"/></svg>
          555.014.2291
        </li>
        <li>
          <svg viewBox="0 0 16 16" aria-hidden="true"><rect x="4" y="1" width="8" height="5"/><rect x="1" y="6" width="14" height="6" rx="1"/><rect x="4" y="11" width="8" height="4"/></svg>
          555-0187346
        </li>
        <li>
          <svg viewBox="0 0 16 16" aria-hidden="true"><path d="M1 3h14v10H1zm1 1.5V5l6 4 6-4v-.5L8 8.3z"/></svg>
          mcastellan@limbworksinc.com
        </li>
        <li>
          <svg viewBox="0 0 16 16" aria-hidden="true"><circle cx="8" cy="8" r="7"/><path d="M8 4v4l3 2" stroke="#1f66b3" stroke-width="1.6" fill="none"/></svg>
          www.limbworksinc.com
        </li>
      </ul>
    </div>
  </section>

</main>
</body>
</html>
```